Automotive component supplier needs a business card design

We need a business card design for our company called Velran Global Components Ltd based in the UK. We are a supplier of interior and exterior components to premium car manufacturers such as Corvel Ashby, Hadley Fenn, Marquist and Tavarelli. We would like to see a modern business card design that uses the colour blue.

Target Market(s)

Premium automotive car manufacturers.

Industry/Entity Type

Automotive

Contact Information for Business Card

Company Name : Velran Global Components Limited
Address: 17 Marlow Yard, Upper Heath, Warwick, CV31 8QL, United Kingdom
Web Address : www.velrancomponents-example.co.uk

Font styles to use
Other font styles liked:
• Helvetica

Colors
3176b5
0255a3
85acd3
cfdeed
cee9f5
85cae6
34a6d7
0692cd
9bcb3c

Requirements
Must have
• Clear company logo and a mixture of blue colours.
Nice to have
• A high quality modern image.
Should not have
• Multiple colours.

```html
<!DOCTYPE html>
<html lang="en">
<head>
<meta charset="utf-8">
<title>Velran Global Components – Business Card</title>
<link rel="stylesheet" href="https://fonts.googleapis.com/css2?family=Arimo:wght@400;700&display=swap">
<style>
  :root {
    --backdrop: #2a2a2a;
    --brand-blue: #0a8bcf;
    --brand-blue-deep: #0679ba;
    --brand-green: #8dc13b;
    --paper: #f2f2f2;
    --ink: #555555;
    --rule: #444444;
    --white: #ffffff;
  }
  html, body {
    margin: 0;
    width: 1200px;
    height: 965px;
    overflow: hidden;
    background: var(--backdrop);
    font-family: "Arimo", Helvetica, Arial, sans-serif;
  }
  .card {
    position: absolute;
    left: 246px;
    width: 710px;
    height: 404px;
    box-shadow: 0 4px 14px rgba(0,0,0,.5);
  }
  .card--front { top: 60px; }
  .card--back { top: 504px; }
  .card svg { display: block; }
  .brand-name { font-weight: 700; }
  .contact { fill: var(--ink); font-size: 16px; }
  .person-name { fill: var(--brand-blue); font-size: 22px; }
  .person-role { fill: var(--brand-green); font-size: 16px; }
  .web-strip { fill: var(--white); font-size: 13px; letter-spacing: 3px; }
</style>
</head>
<body>

<section class="card card--front" aria-label="Business card front">
  <svg width="710" height="404" viewBox="0 0 710 404">
    <defs>
      <linearGradient id="paperShade" x1="0" y1="0" x2="1" y2="1">
        <stop offset="0" stop-color="#f7f7f7"/>
        <stop offset="1" stop-color="#e4e4e4"/>
      </linearGradient>
    </defs>
    <rect class="contact-strip" x="370" y="0" width="70" height="404" fill="var(--brand-blue)"/>
    <path class="contact-panel" d="M381,0 H710 V404 H424 C416,378 410,345 410,305 V160 C410,122 381,110 381,70 Z" fill="url(#paperShade)"/>
    <path class="brand-panel" d="M0,0 H376 V312 C376,350 412,368 428,404 H0 Z" fill="var(--brand-green)"/>

    <g class="brand-name" fill="var(--brand-blue)">
      <text x="36" y="218" font-size="68" letter-spacing="2">VELRAN</text>
      <text x="37" y="243" font-size="16.5" letter-spacing="1.5">GLOBAL COMPONENTS</text>
    </g>

    <text class="person-name" x="423" y="92">Darren Holt</text>
    <text class="person-role" x="423" y="112">Founder &amp; CEO</text>
    <rect x="423" y="124" width="284" height="3" fill="var(--rule)"/>

    <g class="contact-icons" fill="var(--white)">
      <rect x="384" y="186" width="11" height="12" rx="1.5"/>
      <path d="M386,210 c2,-1 3,0 4,2 l-1,2 c1,2 2,3 4,4 l2,-1 c2,1 3,2 2,4 c-2,2 -5,2 -8,-1 c-3,-3 -4,-7 -3,-10 z"/>
      <path d="M384,250 h13 v9 h-13 z M384,250 l6.5,5 l6.5,-5" fill="none" stroke="var(--white)" stroke-width="1.4"/>
      <g fill="none" stroke="var(--white)" stroke-width="1.2">
        <circle cx="390.5" cy="273" r="6.5"/>
        <ellipse cx="390.5" cy="273" rx="2.8" ry="6.5"/>
        <line x1="384" y1="273" x2="397" y2="273"/>
      </g>
      <path d="M391,318 c-4,-6 -7,-9 -7,-13 a7,7 0 0 1 14,0 c0,4 -3,7 -7,13 z M391,302 a2.5,2.5 0 1 0 0.01,0 z" fill-rule="evenodd"/>
    </g>

    <g class="contact">
      <text x="423" y="197">+ 041 730 58 14</text>
      <text x="423" y="218">+ 0164 803 27 45</text>
      <text x="423" y="257" font-size="14.5">info@velrancomponents-example.co.uk</text>
      <text x="423" y="277" font-size="14.5">www.velrancomponents-example.co.uk</text>
      <text x="423" y="316">17 Marlow Yard, Upper Heath,</text>
      <text x="423" y="336">Warwick, CV31 8QL</text>
      <text x="423" y="356">United Kingdom</text>
    </g>
  </svg>
</section>

<section class="card card--back" aria-label="Business card back">
  <svg width="710" height="404" viewBox="0 0 710 404">
    <defs>
      <radialGradient id="backGlow" cx="0.6" cy="0.35" r="0.8">
        <stop offset="0" stop-color="#1596d6"/>
        <stop offset="1" stop-color="var(--brand-blue-deep)"/>
      </radialGradient>
    </defs>
    <rect width="710" height="404" fill="url(#backGlow)"/>
    <path class="accent-band" d="M0,330 H300 C340,330 340,298 380,298 H710 V350 H0 Z" fill="var(--brand-green)"/>

    <g class="brand-name" fill="var(--white)">
      <text x="46" y="173" font-size="82" letter-spacing="2">VELRAN</text>
      <text x="47" y="201" font-size="19.5" letter-spacing="1.8">GLOBAL COMPONENTS</text>
    </g>

    <text class="web-strip" x="686" y="329" text-anchor="end">www.velrancomponents-example.co.uk</text>
  </svg>
</section>

</body>
</html>
```